Very visible CoWorking Building Sign overlooking downtown LA and 110 freeway

Our building is drab but very visible and in the best location. We need a great sign for our monolith that overlooks downtown LA and the 100 freeway. We are a new CoWorking business and would like to have a few things we do on the sign: private offices, virtual offices, CoWorking Lounge. Everything we have seen is ho-hum. Can you get us noticed? We need people to know what we do and that we are here but in a creative, professional, unique sign.
Target Market(s)
People who have a business in DTLA, remote workers and those who work from home who need a professional address.
Requirements
Must have
- Our logo (which can be somewhat reimagined) which has our address 2417 on it. The three things we focus on: Private Offices, Virtual Offices, CoWorking Lounge. Incorporate some Navy. Readable from several hundred feet away.
Nice to have
- Mural feel? Something inspirational in this crazy COVID times? Graphics? Color block. I like the idea of decorative but it has to be readable as a building sign. The same with the use of colors. Our colors are grays and navy but with a pop of the chartreuse (we have 2 velvet chartreuse chairs in the space). Helpful to view our website: Harborview2417.com.
Should not have
- Not too graffiti. Keep it professional but unique and wow.

```html
<!DOCTYPE html>
<html lang="en">
<head>
<meta charset="utf-8">
<title>Harborview 2417 – Coworking Building Sign</title>
<link rel="stylesheet" href="https://fonts.googleapis.com/css2?family=Oswald:wght@500;600&display=swap">
<style>
  :root {
    --navy: #1b355f;
    --white: #ffffff;
    --gray-light: #c9cacc;
    --gray-mid: #a4a6aa;
    --mauve: #8d8590;
    --ink: #1e1f22;
    --stage: #e6e7e8;
  }
  * { margin: 0; padding: 0; box-sizing: border-box; }
  html, body {
    width: 1200px;
    height: 561px;
    overflow: hidden;
    background: var(--stage);
  }
  .sign {
    position: absolute;
    left: 88px;
    top: 90px;
    width: 1024px;
    height: 382px;
    display: block;
  }
  .sign-headline {
    font-family: "Oswald", sans-serif;
    font-weight: 500;
    fill: var(--white);
  }
  .brand-name {
    font-family: "Oswald", sans-serif;
    font-weight: 600;
    fill: var(--navy);
  }
</style>
</head>
<body>
  <svg class="sign" viewBox="0 0 1280 478" xmlns="http://www.w3.org/2000/svg">
    <defs>
      <clipPath id="sign-edge">
        <rect x="0" y="0" width="1280" height="478"/>
      </clipPath>
      <linearGradient id="office-tones" x1="0" y1="0" x2="0.15" y2="1">
        <stop offset="0" stop-color="#f3eee4"/>
        <stop offset="0.06" stop-color="#ece7dc"/>
        <stop offset="0.12" stop-color="#cfd6d2"/>
        <stop offset="0.24" stop-color="#dde2dd"/>
        <stop offset="0.33" stop-color="#f1eee8"/>
        <stop offset="0.42" stop-color="#d9c8a9"/>
        <stop offset="0.5" stop-color="#b98540"/>
        <stop offset="0.62" stop-color="#a87130"/>
        <stop offset="0.74" stop-color="#d39c57"/>
        <stop offset="0.86" stop-color="#a06a2b"/>
        <stop offset="1" stop-color="#7e5220"/>
      </linearGradient>
      <linearGradient id="lounge-tones" x1="0" y1="0" x2="0.3" y2="1">
        <stop offset="0" stop-color="#e2d6bf"/>
        <stop offset="0.35" stop-color="#c9b896"/>
        <stop offset="0.55" stop-color="#8f9b34"/>
        <stop offset="0.75" stop-color="#7f8a2c"/>
        <stop offset="1" stop-color="#8d6a3a"/>
      </linearGradient>
    </defs>

    <g clip-path="url(#sign-edge)">
      <rect class="photo-office" x="0" y="0" width="1280" height="478"
            fill="url(#office-tones)" role="img"
            aria-label="Photo of a bright coworking room with white high tables, black bar stools and a potted fig tree on a polished amber floor"/>

      <polygon class="photo-lounge" points="1173,276 1280,215 1280,478 960,478"
               fill="url(#lounge-tones)" role="img"
               aria-label="Photo of a lounge corner with two chartreuse velvet armchairs and a round rug"/>

      <polygon class="accent-gray" points="712,0 868,0 792,74" fill="var(--gray-light)"/>
      <line class="accent-rule" x1="866" y1="0" x2="775" y2="90" stroke="var(--ink)" stroke-width="3"/>
      <line class="accent-rule" x1="852" y1="14" x2="790" y2="76" stroke="var(--ink)" stroke-width="1.5"/>
      <polygon class="accent-gray-stripe" points="918,0 948,0 1128,196 1104,218" fill="var(--gray-mid)"/>

      <polygon class="accent-navy-band" points="574,478 694,356 744,406 672,478" fill="var(--navy)"/>
      <polygon class="accent-mauve-band" points="672,478 744,406 776,438 736,478" fill="var(--mauve)" opacity="0.8"/>

      <polygon class="logo-panel" points="936,0 1280,0 1280,215 1173,276" fill="var(--white)"/>

      <polygon class="headline-frame" points="910,6 1175,271 910,536 645,271" fill="var(--white)"/>
      <polygon class="headline-diamond" points="910,16 1165,271 910,526 655,271" fill="var(--navy)"/>
    </g>

    <text class="brand-name" x="1165" y="88" font-size="36" text-anchor="middle">HARBORVIEW</text>
    <text class="brand-name" x="1165" y="148" font-size="58" text-anchor="middle">2417</text>

    <text class="sign-headline" x="905" y="186" font-size="48" text-anchor="middle">PRIVATE &amp;</text>
    <text class="sign-headline" x="905" y="248" font-size="48" text-anchor="middle">VIRTUAL OFFICES</text>
    <line class="headline-divider" x1="790" y1="273" x2="1020" y2="273" stroke="var(--gray-light)" stroke-width="2"/>
    <text class="sign-headline" x="905" y="338" font-size="48" text-anchor="middle">COWORKING</text>
    <text class="sign-headline" x="905" y="403" font-size="48" text-anchor="middle">LOUNGE</text>
  </svg>
</body>
</html>
```